Modern Business Card

Modern professional business card with more than just logo and demographic info. Something memorable.

We are a trendy/modern chiropractic group with an emphasis on neurology, hence the minimalist-type brain logo. We want to convey that modern and technical aspect with professionalism and the elite nature of our practice environment.

```html
<!DOCTYPE html>
<html lang="en">
<head>
<meta charset="utf-8">
<title>Keystone Chiropractic – Business Card</title>
<link rel="stylesheet" href="https://fonts.googleapis.com/css2?family=Arimo:wght@400;700&family=Raleway:wght@700&display=swap">
<style>
  :root {
    --backdrop: #e8e4de;
    --card-blue: #4a80c2;
    --card-black: #020202;
    --ink-white: #ffffff;
    --accent-blue: #4a80c2;
    --rule: rgba(255,255,255,0.9);
  }
  html, body {
    margin: 0;
    padding: 0;
    width: 1200px;
    height: 900px;
    overflow: hidden;
    background: var(--backdrop);
  }
  .canvas {
    position: relative;
    width: 1200px;
    height: 900px;
  }
  .card {
    position: absolute;
    box-shadow: 0 4px 10px rgba(0,0,0,0.25);
  }
  .card--front {
    left: 330px; top: 90px;
    width: 555px; height: 343px;
    background: var(--card-blue);
    color: var(--ink-white);
    font-family: "Arimo", Arial, sans-serif;
    text-align: center;
  }
  .card--back {
    left: 330px; top: 469px;
    width: 559px; height: 343px;
    background: var(--card-black);
  }
  .holder-name {
    position: absolute; left: 0; right: 0; top: 66px;
    margin: 0;
    font-family: "Raleway", Arial, sans-serif;
    font-weight: 700;
    font-size: 20px;
    letter-spacing: 0.3px;
  }
  .holder-role {
    position: absolute; left: 0; right: 0; top: 87px;
    margin: 0;
    font-size: 16px;
  }
  .divider {
    position: absolute;
    left: 50%;
    width: 136px;
    margin-left: -68px;
    height: 1px;
    background: var(--rule);
  }
  .divider--upper { top: 116px; }
  .divider--lower { top: 222px; }
  .contact-list {
    position: absolute; left: 0; right: 0; top: 129px;
    margin: 0; padding: 0;
    list-style: none;
    font-size: 16px;
    line-height: 20.3px;
  }
  .contact-list b { font-weight: 700; }
  .address {
    position: absolute; left: 0; right: 0; top: 239px;
    margin: 0;
    font-size: 16px;
    line-height: 20px;
    font-style: normal;
  }
  .brand {
    position: absolute;
    left: 113px; top: 124px;
    display: flex;
    align-items: center;
    gap: 14px;
  }
  .brand-mark {
    width: 62px; height: 62px;
    background: var(--accent-blue);
    flex: none;
  }
  .brand-name {
    margin: 0;
    font-family: "Arimo", Arial, sans-serif;
    font-weight: 400;
    color: var(--ink-white);
    line-height: 1;
    text-transform: uppercase;
  }
  .brand-name span { display: block; }
  .brand-name .brand-line-1 { font-size: 44px; letter-spacing: 1px; }
  .brand-name .brand-line-2 { font-size: 24.5px; letter-spacing: 0.5px; margin-top: 4px; }
</style>
</head>
<body>
  <main class="canvas">
    <section class="card card--front" aria-label="Card front">
      <h1 class="holder-name">DANIEL REYES</h1>
      <p class="holder-role">Managing Director</p>
      <div class="divider divider--upper"></div>
      <ul class="contact-list">
        <li><b>P:</b> 044-555 010 200</li>
        <li><b>M:</b> 044-555 010 200</li>
        <li><b>E:</b> hello@keystonespine.com</li>
        <li><b>W:</b> www.keystonespine.com</li>
      </ul>
      <div class="divider divider--lower"></div>
      <address class="address">48 Harbor Lane, Suite 2<br>Westbrook, 204518.</address>
    </section>

    <section class="card card--back" aria-label="Card back">
      <div class="brand">
        <div class="brand-mark"></div>
        <p class="brand-name">
          <span class="brand-line-1">Keystone</span>
          <span class="brand-line-2">Chiropractic</span>
        </p>
      </div>
    </section>
  </main>
</body>
</html>
```